Business Card Design

Please see my website www.qvleading.com.au to for further information on my services and styling of my site
Updates

Project Deadline Extended
Reason: Deadline is extended to permit alterations to current designs or for any new submissions. Cheers

Industry/Entity Type

Business

Contact Information for Business Card

Marcus Belton
Empowerment Coach

'Live your passion'

marcus@qvleading.com.au
0437158206
qvleading.com.au

```html
<!DOCTYPE html>
<html lang="en">
<head>
<meta charset="utf-8">
<title>Quest Vital Leading – Business Card</title>
<link rel="stylesheet" href="https://fonts.googleapis.com/css2?family=Pathway+Gothic+One&family=Black+Ops+One&family=Open+Sans:wght@400;600&display=swap">
<style>
  :root {
    --canvas: #ecebe7;
    --card-white: #fbfbfa;
    --lime: #b5d95a;
    --lime-soft: #cfe68e;
    --grey-stripe: #c9c9c9;
    --ink-grey: #6d6d6d;
    --green: #86bb3c;
    --green-light: #9fcb55;
    --green-dark: #4e8a22;
    --white: #ffffff;
  }
  html, body {
    margin: 0;
    width: 1200px;
    height: 1024px;
    overflow: hidden;
    background: var(--canvas);
  }
  .canvas {
    position: relative;
    width: 1200px;
    height: 1024px;
  }
  .card {
    position: absolute;
    left: 320px;
    width: 560px;
    height: 320px;
    overflow: hidden;
    box-shadow: 0 6px 18px rgba(0,0,0,0.12);
  }
  /* Front */
  .card--front {
    top: 150px;
    background: var(--card-white);
  }
  .front-stripes {
    position: absolute;
    left: 0;
    top: 188px;
  }
  .brand {
    position: absolute;
    left: 330px;
    top: 92px;
    width: 190px;
  }
  .brand__name {
    display: flex;
    align-items: center;
    gap: 10px;
    font-family: "Pathway Gothic One", sans-serif;
    font-size: 30px;
    line-height: 1;
    color: var(--ink-grey);
    padding-bottom: 10px;
    border-bottom: 1px solid var(--grey-stripe);
  }
  .brand__mark {
    width: 14px;
    height: 14px;
    border-radius: 50%;
    background: var(--lime);
    flex: none;
  }
  .brand__web {
    display: flex;
    align-items: center;
    gap: 6px;
    margin-top: 8px;
    font-family: "Open Sans", sans-serif;
    font-weight: 600;
    font-size: 11px;
    color: #333333;
  }
  /* Back */
  .card--back {
    top: 554px;
    background: var(--green);
  }
  .back-panel {
    position: absolute;
    left: 230px;
    top: 0;
    width: 330px;
    height: 320px;
    background: var(--green-light);
  }
  .back-brand {
    position: absolute;
    left: 18px;
    top: 160px;
    transform-origin: left top;
    transform: rotate(-90deg) translate(-50%, 0);
    font-family: "Pathway Gothic One", sans-serif;
    font-size: 22px;
    color: var(--white);
    white-space: nowrap;
  }
  .name-band {
    position: absolute;
    left: 90px;
    right: 0;
    top: 92px;
    height: 58px;
    background: var(--green-dark);
    display: flex;
    align-items: center;
    padding-left: 24px;
  }
  .name-band__name {
    font-family: "Black Ops One", sans-serif;
    font-size: 30px;
    letter-spacing: 1px;
    color: var(--white);
    text-transform: uppercase;
  }
  .details {
    position: absolute;
    left: 114px;
    top: 164px;
    font-family: "Open Sans", sans-serif;
    font-size: 13px;
    line-height: 20px;
    color: var(--white);
  }
  .details__role { font-weight: 600; font-size: 14px; }
  .details__motto { font-style: italic; margin-bottom: 8px; }
  .details p { margin: 0; }
</style>
</head>
<body>
<div class="canvas">

  <section class="card card--front" aria-label="Card front">
    <svg class="front-stripes" width="290" height="52" viewBox="0 0 290 52" aria-hidden="true">
      <rect x="0" y="0" width="290" height="12" fill="var(--lime)"/>
      <rect x="0" y="16" width="274" height="4" fill="var(--grey-stripe)"/>
      <rect x="0" y="26" width="258" height="4" fill="var(--grey-stripe)"/>
      <rect x="0" y="34" width="242" height="12" fill="var(--lime-soft)"/>
    </svg>

    <div class="brand">
      <div class="brand__name"><span class="brand__mark"></span>Quest Vital Leading</div>
      <div class="brand__web">
        <svg width="11" height="11" viewBox="0 0 12 12" aria-hidden="true">
          <circle cx="6" cy="6" r="5" fill="none" stroke="#333" stroke-width="1.4"/>
          <path d="M1 6h10M6 1c2 2 2 8 0 10M6 1c-2 2-2 8 0 10" fill="none" stroke="#333" stroke-width="1"/>
        </svg>
        qvleading.com.au
      </div>
    </div>
  </section>

  <section class="card card--back" aria-label="Card back">
    <div class="back-panel"></div>
    <div class="back-brand">Quest Vital Leading</div>
    <div class="name-band">
      <span class="name-band__name">Marcus Belton</span>
    </div>
    <div class="details">
      <p class="details__role">Empowerment Coach</p>
      <p class="details__motto">'Live your passion'</p>
      <p>marcus@qvleading.com.au</p>
      <p>0437158206</p>
      <p>www.qvleading.com.au</p>
    </div>
  </section>

</div>
</body>
</html>
```